Business Card for premium dental clinic

We are a premium dental clinic based in Brasov, Romania with more than 15 year on the market, providing quality dental treatment made by a team of more specialized dentists, working with modern equipment as a solution to beautiful and healthy teeth.

Our current logo for the clinic use 2 square with colors black and gold - dr Ternisu - studio, using family fonts Bodoni, Myriad Pro and Segoe Print.
Depending on the printing we used some gold CMYK background or gold foil picture background or a gold gradient.
We want a business card:
- eye catching business card
- distinguished business card
- premium design
- to keep the color scheme of black and gold
- to attract the customers to spent time reading the information
- modern concept

```html
<!DOCTYPE html>
<html lang="en">
<head>
<meta charset="utf-8">
<title>dr Ternisu – Business Card</title>
<link rel="stylesheet" href="https://fonts.googleapis.com/css2?family=Lato:wght@400;700&display=swap">
<style>
  :root {
    --page: #e6e6e6;
    --black: #050505;
    --gold: #bd8a2c;
    --paper: #f3f3f3;
    --white: #ffffff;
    --ink: #1e1e1e;
    --rule: #c9c9c9;
  }
  * { box-sizing: border-box; margin: 0; padding: 0; }
  html, body { width: 1200px; height: 1015px; overflow: hidden; }
  body {
    background: var(--page);
    font-family: "Lato", Arial, sans-serif;
    position: relative;
  }
  .card {
    position: absolute;
    left: 250px;
    width: 700px;
    height: 400px;
    overflow: hidden;
    box-shadow: 0 10px 30px rgba(0,0,0,.18);
  }
  .card-front { top: 70px; background: var(--black); }
  .card-back { top: 530px; background: var(--paper); }
  .gold-band {
    position: absolute; left: 0; right: 0; bottom: 0;
    height: 14px; background: var(--gold);
  }
  .brand-name {
    font-weight: 400;
    letter-spacing: .5px;
    white-space: nowrap;
    line-height: 1;
  }
  .card-front .brand-name {
    position: absolute;
    left: 0; right: 0; top: 168px;
    text-align: center;
    font-size: 40px;
    color: var(--white);
  }
  .card-back .brand-name {
    position: absolute;
    left: 0; width: 392px; top: 176px;
    text-align: center;
    font-size: 34px;
    color: var(--black);
  }
  .divider {
    position: absolute; left: 392px; top: 50px; width: 1px; height: 280px;
    background: var(--rule);
  }
  .contact { position: absolute; left: 420px; top: 72px; color: var(--ink); }
  .contact-name { color: var(--gold); font-weight: 700; font-size: 22px; letter-spacing: .5px; }
  .contact-role { font-size: 16px; margin-bottom: 12px; }
  .contact-list { list-style: none; font-size: 16px; line-height: 1.6; }
  .contact-list li { display: flex; align-items: center; gap: 8px; }
  .contact-list svg { width: 14px; height: 14px; flex: none; }
  .address { margin-top: 8px; padding-left: 22px; font-size: 16px; line-height: 1.4; }
</style>
</head>
<body>
  <section class="card card-front" aria-label="Card front">
    <p class="brand-name">dr Ternisu</p>
    <div class="gold-band"></div>
  </section>

  <section class="card card-back" aria-label="Card back">
    <p class="brand-name">dr Ternisu</p>
    <div class="divider"></div>
    <div class="contact">
      <p class="contact-name">MIHAI DORESCU</p>
      <p class="contact-role">Managing Director</p>
      <ul class="contact-list">
        <li>
          <svg viewBox="0 0 14 14"><path fill="#bd8a2c" d="M3 1l2.5 3-1.3 1.5c.8 1.7 2.3 3.2 4 4L9.7 8.2 13 10.5 11.5 13C6 12.5 1.5 8 1 2.5z"/></svg>
          044-218 730 655
        </li>
        <li>
          <svg viewBox="0 0 14 14"><rect x="1" y="3" width="12" height="9" fill="#bd8a2c"/><path d="M1 3l6 5 6-5" fill="none" stroke="#f3f3f3" stroke-width="1.2"/></svg>
          hello@ternisudental.ro
        </li>
        <li>
          <svg viewBox="0 0 14 14"><circle cx="7" cy="7" r="6" fill="#bd8a2c"/><path d="M1 7h12M7 1c-3 3-3 9 0 12M7 1c3 3 3 9 0 12" fill="none" stroke="#f3f3f3" stroke-width="1"/></svg>
          www.ternisudental.ro
        </li>
      </ul>
      <p class="address">27, Strada Lunga<br>Brasov, 500035</p>
    </div>
    <div class="gold-band"></div>
  </section>
</body>
</html>
```